Roofing web site brvt roofing

Look at some of our competitors web page we like something similar with NYC roofing
https://www.quillbarroofing.example/
Maybe a skyline picture of nyc at the home page with a picture of flat roofing installation

Target Market(s)

Commercial and residential flat roofs

Industry/Entity Type

Flat Roofing industry

Coding

Coded - Design and coding required

Number of Pages Required

2 page

Font styles to use
Decorative
Script

Colors

Designer to choose colors to be used in the design.

Requirements
Must have
• At BRVT Roofing, we are a trusted and reputable roofing company specializing in new construction flat roof installation and repair. With years of experience in the industry, we take pride in providing exceptional roofing solutions to our valued clients. Our team of highly skilled and dedicated roofing professionals understands the unique challenges and requirements of new construction projects. We work closely with builders, contractors, and architects to design and install flat roofs that meet the specific needs of each project. From commercial buildings to residential complexes, we have the expertise to deliver reliable and durable roofing solutions. When it comes to flat roof repairs, we are your go-to experts. Our experienced technicians conduct thorough inspections to identify the root cause of any issues your roof may be experiencing. We utilize the latest industry techniques and high-quality materials to efficiently repair your flat roof, ensuring its integrity and longevity. At BRVT Roofing, we prioritize customer satisfaction above all else. We believe in building strong relationships with our clients by providing exceptional craftsmanship and outstanding customer service. Our team is dedicated to delivering projects on time, within budget, and to the highest standards of quality. We understand that a well-maintained roof is essential for protecting your property and ensuring the safety of its occupants. That's why we use only the best materials and employ skilled professionals who are trained in the latest roofing practices. Our commitment to excellence is evident in every project we undertake. As a fully licensed and insured roofing company, we prioritize safety and adhere to industry regulations and best practices. We take every precaution to create a safe working environment for our team and minimize any disruptions to your daily routine. When you choose BRVT Roofing, you can trust that you are working with a reliable and reputable company that will deliver exceptional results. We are committed to exceeding your expectations and providing you with a roof that is built to last. Contact us today for all your new construction flat roof installation and repair needs.
Nice to have
• NYC skyline background with commercial roofing pictures of torching roofing

```html
<!DOCTYPE html>
<html lang="en">
<head>
<meta charset="utf-8">
<title>BRVT Roofing</title>
<link href="https://fonts.googleapis.com/css2?family=Raleway:wght@500;600;700;800;900&family=Josefin+Sans:wght@400;500;600&display=swap" rel="stylesheet">
<style>
:root{
  --orange:#f26b21;
  --orange-dark:#e35d15;
  --ink:#1c1c1c;
  --text:#3b3b3b;
  --muted:#6d6d6d;
  --white:#ffffff;
  --faq-bg:#f1f1f1;
  --navy:#2a3d73;
}
*{box-sizing:border-box;margin:0;padding:0}
html,body{width:1200px;height:4532px;overflow:hidden;background:var(--white)}
body{font-family:"Josefin Sans",Arial,sans-serif;color:var(--text);position:relative}
a{color:inherit}

/* top info bar */
.topbar{height:52px;display:flex;align-items:center;justify-content:space-between;padding:0 64px 0 110px;font-size:15px;color:var(--ink)}
.topbar span{display:flex;align-items:center;gap:12px}
.topbar svg{width:20px;height:20px;stroke:var(--ink);fill:none;stroke-width:1.6}

/* nav */
.nav{height:84px;background:var(--orange);display:flex;align-items:center;padding:0 111px}
.brand{font-family:"Raleway",Arial,sans-serif;font-weight:800;font-size:25px;color:var(--white);width:140px;line-height:1}
.menu{display:flex;gap:32px;margin-left:80px;color:var(--white);font-size:15px;letter-spacing:.5px}
.btn-nav{margin-left:auto;background:var(--white);color:var(--orange);font-size:14px;font-weight:600;padding:16px 24px;letter-spacing:.5px}

.notice{height:52px;display:flex;align-items:center;justify-content:center;font-size:18px;letter-spacing:1px;color:var(--ink);font-weight:500}

/* hero */
.hero{position:relative;height:642px;background:linear-gradient(180deg,#5f7385 0%,#7c8791 30%,#8b8a86 55%,#a4a29e 75%,#7e7d7a 100%);overflow:hidden}
.hero-photo{position:absolute;inset:0}
.hero-inner{position:relative;text-align:center;padding-top:145px;color:var(--white)}
.hero h1{font-family:"Raleway",Arial,sans-serif;font-weight:800;font-size:42px;letter-spacing:2px;line-height:52px}
.hero p{font-size:18px;line-height:27px;margin:24px auto 0;width:620px}
.btn-white{display:inline-block;background:var(--white);color:var(--orange);font-size:14px;font-weight:600;padding:14px 26px;letter-spacing:.5px}
.hero .btn-white{margin-top:26px}

/* about */
.about{position:relative;height:600px}
.about-photo{position:absolute;left:109px;top:85px;width:697px;height:430px;background:linear-gradient(160deg,#4b5663 0%,#2c3238 45%,#8a6a4c 75%,#3d4248 100%)}
.about-card{position:absolute;left:683px;top:117px;width:406px;height:366px;background:var(--white);box-shadow:0 6px 30px rgba(0,0,0,.12);padding:34px 44px}
.eyebrow{font-size:13px;font-weight:600;color:var(--ink);letter-spacing:.5px}
.about-card h2{font-family:"Raleway",Arial,sans-serif;font-weight:800;font-size:40px;line-height:40px;color:var(--orange);margin-top:22px;letter-spacing:1px}
.about-lead{font-size:13px;font-weight:600;color:var(--ink);line-height:21px;margin-top:14px}
.about-body{font-size:12.5px;color:var(--muted);line-height:21px;margin-top:18px}
.btn-line{display:inline-flex;align-items:center;gap:6px;border:1px solid #e3e3e3;color:var(--orange);font-size:13px;font-weight:600;padding:9px 10px;margin-top:18px}
.btn-line svg{width:22px;height:12px;stroke:currentColor;fill:none;stroke-width:2}

/* service tiles */
.tiles{display:flex;gap:24px;padding:0 111px;height:278px}
.tile{width:176px;height:188px;box-shadow:0 4px 16px rgba(0,0,0,.1);text-align:center}
.tile-photo{height:126px}
.tile b{display:block;font-family:"Raleway",Arial,sans-serif;font-weight:700;font-size:15px;color:var(--orange);line-height:15px;margin-top:16px}

/* our services */
.services{height:623px;background:var(--orange);text-align:center;color:var(--white);padding-top:76px}
.section-title{font-family:"Raleway",Arial,sans-serif;font-weight:800;font-size:40px;letter-spacing:2px}
.services .sub{font-size:18px;letter-spacing:1.5px;margin-top:24px}
.svc-row{display:flex;gap:24px;justify-content:center;margin-top:34px}
.svc{width:323px;height:317px;background:var(--white);color:var(--ink);padding-top:42px}
.svc svg{width:72px;height:64px}
.svc h3{font-family:"Raleway",Arial,sans-serif;font-weight:700;font-size:17px;letter-spacing:.5px;margin-top:18px}
.svc p{font-size:14px;color:var(--muted);line-height:25.5px;width:260px;margin:24px auto 0}

/* why choose */
.why{height:876px;text-align:center;padding-top:80px}
.why .section-title{color:var(--orange)}
.why .sub{font-size:18px;letter-spacing:1px;color:var(--ink);margin-top:26px}
.why-box{position:absolute;left:56px;top:2549px;width:1090px;height:589px;box-shadow:0 8px 36px rgba(0,0,0,.12);background:var(--white);text-align:left}
.why-tabs{position:absolute;left:0;top:0;width:215px}
.why-tab{height:197px;display:flex;flex-direction:column;align-items:center;justify-content:center;text-align:center;font-family:"Raleway",Arial,sans-serif;font-weight:700;font-size:17px;line-height:26px;color:var(--orange)}
.why-tab svg{width:58px;height:50px;margin-bottom:22px}
.why-tab.active{background:var(--orange);color:var(--white)}
.why-photo{position:absolute;left:215px;top:0;width:875px;height:255px;background:linear-gradient(120deg,#b9bfc5 0%,#5a5f66 40%,#2e3237 70%,#6d737a 100%)}
.why-copy{position:absolute;left:312px;top:290px}
.why-copy h3{font-family:"Raleway",Arial,sans-serif;font-weight:700;font-size:25px;color:var(--ink);letter-spacing:.5px}
.why-copy ul{list-style:none;margin-top:26px;font-size:19px;color:var(--ink);line-height:31px;padding-left:3px}
.btn-orange{display:inline-flex;align-items:center;gap:6px;background:var(--orange);color:var(--white);font-size:14px;font-weight:600;padding:10px 11px;margin-top:31px}
.btn-orange svg{width:24px;height:12px;stroke:currentColor;fill:none;stroke-width:2}

/* cta band */
.cta{position:absolute;left:0;top:3208px;width:1200px;height:257px;background:linear-gradient(90deg,rgba(242,107,33,.92),rgba(236,110,40,.85) 50%,rgba(242,107,33,.92)),linear-gradient(180deg,#d7692a,#b5561f);text-align:center;color:var(--white);padding-top:34px}
.cta h2{font-family:"Raleway",Arial,sans-serif;font-weight:800;font-size:40px;letter-spacing:1.5px}
.cta p{font-size:18px;line-height:27px;width:740px;margin:14px auto 0;letter-spacing:.3px}
.cta .btn-white{margin-top:18px;padding:10px 10px;display:inline-flex;align-items:center;gap:6px;font-size:14px}
.cta .btn-white svg{width:22px;height:12px;stroke:currentColor;fill:none;stroke-width:2}

/* faq */
.faq{position:absolute;left:0;top:3500px;width:1200px;text-align:center}
.faq .section-title{color:var(--orange);margin-top:40px}
.faq .sub{font-size:18px;letter-spacing:1px;color:var(--ink);margin-top:26px}
.faq-list{width:848px;margin:30px auto 0;text-align:left}
.faq-item{height:50px;background:var(--faq-bg);display:flex;align-items:center;justify-content:space-between;padding:0 64px 0 30px;font-size:17px;color:var(--ink);margin-bottom:29px}
.faq-item svg{width:16px;height:16px;stroke:var(--ink);stroke-width:2.4}
.faq-item.open{height:112px;background:var(--white);box-shadow:0 4px 12px rgba(0,0,0,.1);flex-direction:column;align-items:stretch;justify-content:flex-start;padding-top:20px}
.faq-q{display:flex;justify-content:space-between;align-items:center}
.faq-a{color:var(--navy);font-size:15px;line-height:21px;margin-top:14px;padding-left:6px;width:640px}

/* footer */
.footer{position:absolute;left:0;top:4192px;width:1200px;height:340px;background:var(--orange);color:var(--white)}
.f-brand{position:absolute;left:110px;top:68px;font-family:"Raleway",Arial,sans-serif;font-weight:800;font-size:26px;line-height:1}
.f-about{position:absolute;left:110px;top:116px;width:220px;font-size:11px;line-height:20px}
.f-social{position:absolute;left:110px;top:190px;display:flex;gap:22px}
.f-social span{width:18px;height:18px;border:1.6px solid var(--white);border-radius:50%}
.f-col{position:absolute;top:52px}
.f-col h4{font-family:"Raleway",Arial,sans-serif;font-weight:700;font-size:20px;letter-spacing:.5px}
.f-col ul{list-style:none;margin-top:24px;font-size:17px;line-height:26px}
.f-col.links ul li{text-decoration:underline}
.contact-row{display:flex;gap:12px;font-size:15px;line-height:20px;margin-bottom:14px}
.contact-row svg{width:22px;height:22px;stroke:var(--white);fill:none;stroke-width:1.6;flex:none}
.f-rule{position:absolute;left:110px;right:110px;top:280px;border-top:1px solid rgba(255,255,255,.6)}
.f-copy{position:absolute;left:0;right:0;top:302px;text-align:center;font-size:16px;letter-spacing:.5px}
</style>
</head>
<body>

<div class="topbar">
  <span><svg viewBox="0 0 24 24"><rect x="3" y="5" width="18" height="14"/><path d="M3 6l9 7 9-7"/></svg>hello@brvtroofing.example</span>
  <span style="margin-left:120px"><svg viewBox="0 0 24 24"><path d="M5 3h4l2 5-3 2a11 11 0 006 6l2-3 5 2v4a2 2 0 01-2 2A17 17 0 013 5a2 2 0 012-2z"/></svg>(800) 555-0192</span>
  <span><svg viewBox="0 0 24 24"><circle cx="12" cy="12" r="9"/><path d="M12 7v5l3 2"/></svg>Mon - Sat : 08.00-21.00</span>
</div>

<nav class="nav">
  <div class="brand">BRVT Roofing</div>
  <div class="menu"><span>HOME</span><span>ABOUT US</span><span>PHOTO GALLERY</span><span>SERVICES</span><span>CONTACT US</span></div>
  <span class="btn-nav">GET STARTED</span>
</nav>

<div class="notice">FREE INSPECTION FOR DAMAGE TO SUBMIT TO YOUR INSURANCE COMPANY!</div>

<section class="hero">
  <div class="hero-photo" role="img" aria-label="New York City skyline behind a flat roof where a roofer in a hard hat installs membrane roofing"></div>
  <div class="hero-inner">
    <h1>ROOF INSTALLATION REPAIR &amp;<br>RESTORATION</h1>
    <p>Flat roofing maintenance includes drain- ing water, repairing your roof's infiltration system, and getting rid of debris</p>
    <span class="btn-white">GET STARTED</span>
  </div>
</section>

<section class="about">
  <div class="about-photo" role="img" aria-label="Modern house with dark metal roof and timber cladding under a cloudy sky"></div>
  <div class="about-card">
    <div class="eyebrow">ABOUT US</div>
    <h2>REPUTABLE<br>AND ROOFING</h2>
    <p class="about-lead">At BRVT Roofing, we are a trusted and reputable roofing company specializing in</p>
    <p class="about-body">With years of experience in the industry, we take pride in providing exceptional roofing solutions to our valued clients. Our team of highly skilled</p>
    <span class="btn-line">READ MORE <svg viewBox="0 0 22 12"><path d="M0 6h20M15 1l5 5-5 5"/></svg></span>
  </div>
</section>

<section class="tiles">
  <div class="tile"><div class="tile-photo" role="img" aria-label="Roofer repairing a flat roof" style="background:linear-gradient(160deg,#8aa0b8,#3e4a59)"></div><b>Roof<br>Repairing</b></div>
  <div class="tile"><div class="tile-photo" role="img" aria-label="Layered flat roof membrane" style="background:linear-gradient(180deg,#a9c6e6,#4a6f98)"></div><b>Roofing<br>Layers</b></div>
  <div class="tile"><div class="tile-photo" role="img" aria-label="Worker renovating a clay tile roof" style="background:linear-gradient(160deg,#d86a3a,#8d3a1c)"></div><b>Roof<br>Renovation</b></div>
  <div class="tile"><div class="tile-photo" role="img" aria-label="Modern home with damaged roof section" style="background:linear-gradient(180deg,#c9ced4,#4a4d52)"></div><b>Damage<br>Roofing</b></div>
  <div class="tile"><div class="tile-photo" role="img" aria-label="Roof corner with timber siding" style="background:linear-gradient(180deg,#4d4f52 0%,#4d4f52 50%,#b88a5a 55%,#9c6f43 100%)"></div><b>Siding<br>Corner</b></div>
</section>

<section class="services">
  <h2 class="section-title">OUR SERVICES</h2>
  <p class="sub">WE'RE HERE WHEN YOU NEED US</p>
  <div class="svc-row">
    <div class="svc">
      <svg viewBox="0 0 72 64"><path d="M6 34L36 8l30 26" fill="none" stroke="#1c1c1c" stroke-width="4"/><path d="M14 30v30h44V30L36 11z" fill="#f26b21" stroke="#1c1c1c" stroke-width="3"/><path d="M48 10v12" stroke="#1c1c1c" stroke-width="5"/><rect x="30" y="40" width="12" height="20" fill="#fff" stroke="#1c1c1c" stroke-width="3"/></svg>
      <h3>ROOF LEAK REPAIRS</h3>
      <p>Flat roofing maintenance includes drain- ing water, repairing your roof's infiltration system, and getting rid of debris</p>
    </div>
    <div class="svc">
      <svg viewBox="0 0 72 64"><path d="M12 28L36 6l24 22v32H12z" fill="#f26b21" stroke="#1c1c1c" stroke-width="3.5"/><path d="M39 22l-9 14h9l-5 13 11-17h-9z" fill="#fff" stroke="#1c1c1c" stroke-width="2.5"/></svg>
      <h3>FLASHING SERVICES</h3>
      <p>Roof flashing plays an important role in leak prevention at the most vulnerable areas of your roof</p>
    </div>
    <div class="svc">
      <svg viewBox="0 0 72 64"><g fill="#f26b21" stroke="#1c1c1c" stroke-width="2.5"><path d="M18 6c6 8 8 12 8 16a8 8 0 01-16 0c0-4 2-8 8-16z"/><path d="M36 4c6 8 8 12 8 16a8 8 0 01-16 0c0-4 2-8 8-16z"/><path d="M54 6c6 8 8 12 8 16a8 8 0 01-16 0c0-4 2-8 8-16z"/></g><path d="M8 44L36 34l28 10" fill="none" stroke="#1c1c1c" stroke-width="3"/><rect x="10" y="46" width="52" height="14" fill="#f26b21" stroke="#1c1c1c" stroke-width="2.5"/><path d="M18 46v14M28 46v14M38 46v14M48 46v14" stroke="#1c1c1c" stroke-width="2"/></svg>
      <h3>WATERPROOFING EXPERTS</h3>
      <p>Our highly-skilled technicians will expertly diagnose your problem areas and provide you solution to your specific need.</p>
    </div>
  </div>
</section>

<section class="why">
  <h2 class="section-title">WHY CHOOSE US</h2>
  <p class="sub">Licensed, Bonded, &amp; Insured More Reliable &amp; Experienced Professionals Free Evaluations &amp; Estimates</p>
</section>

<div class="why-box">
  <div class="why-tabs">
    <div class="why-tab"><svg viewBox="0 0 58 50"><path d="M4 40L20 18h34L38 40z" fill="#f26b21" stroke="#1c1c1c" stroke-width="2.5"/><path d="M12 30h34M18 22l-8 18M30 18l-8 22M42 18l-8 22" stroke="#1c1c1c" stroke-width="1.8"/><rect x="26" y="4" width="12" height="12" fill="#f26b21" stroke="#1c1c1c" stroke-width="2.5"/></svg>Reliable Roofing<br>Professionals</div>
    <div class="why-tab active"><svg viewBox="0 0 58 50"><path d="M6 24L29 6l23 18v22H6z" fill="#fff" stroke="#1c1c1c" stroke-width="2.5"/><path d="M6 32h46M6 39h46M16 24v22M28 24v22M40 24v22" stroke="#1c1c1c" stroke-width="1.8"/></svg>Individualized<br>Roofing Options</div>
    <div class="why-tab"><svg viewBox="0 0 58 50"><path d="M6 18L30 4l22 2" fill="none" stroke="#1c1c1c" stroke-width="2.5"/><path d="M10 16l6-10M18 12l6-10M26 8l6-6M34 6l4-4M42 6l4-4" stroke="#1c1c1c" stroke-width="2"/><path d="M30 46V26h20" fill="none" stroke="#f26b21" stroke-width="5"/><path d="M22 30l14-10" stroke="#1c1c1c" stroke-width="3"/></svg>Satisfaction<br>Guaranteed</div>
  </div>
  <div class="why-photo" role="img" aria-label="Roofer in a hard hat working on a standing-seam metal roof"></div>
  <div class="why-copy">
    <h3>WHY CHOOSE BRVT CONSTRUCTION?</h3>
    <ul>
      <li>Licensed, Bonded, &amp; Insured</li>
      <li>More Reliable &amp; Experienced Professionals</li>
      <li>Free Evaluations &amp; Estimates</li>
      <li>Labels 2024 Holidays Lead-Safe Certified</li>
      <li>24/7 Emergency Response</li>
    </ul>
    <span class="btn-orange">READ MORE <svg viewBox="0 0 24 12"><path d="M0 6h22M17 1l5 5-5 5"/></svg></span>
  </div>
</div>

<section class="cta" role="img" aria-label="Roofers at work on a flat roof, tinted orange">
  <h2>NEED ROOFING ANY SERVICES?</h2>
  <p>Our highly-skilled technicians will expertly diagnose your problem areas and provide you solution to your specific need.</p>
  <span class="btn-white">CLICK HERE <svg viewBox="0 0 22 12"><path d="M0 6h20M15 1l5 5-5 5"/></svg></span>
</section>

<section class="faq">
  <h2 class="section-title">FREQUENTLY ASKED QUESTIONS</h2>
  <p class="sub">PLEASE CONTACT US IF YOU CANNOT FIND AN ANSWER TO YOUR QUESTION.</p>
  <div class="faq-list">
    <div class="faq-item">Roof flashing plays an important role in leak prevention most vulnerable areas?<svg viewBox="0 0 16 16"><path d="M8 0v16M0 8h16"/></svg></div>
    <div class="faq-item">Roof flashing plays an important role in leak prevention most vulnerable areas?<svg viewBox="0 0 16 16"><path d="M8 0v16M0 8h16"/></svg></div>
    <div class="faq-item">Roof flashing plays an important role in leak prevention most vulnerable areas?<svg viewBox="0 0 16 16"><path d="M8 0v16M0 8h16"/></svg></div>
    <div class="faq-item">Roof flashing plays an important role in leak prevention most vulnerable areas?<svg viewBox="0 0 16 16"><path d="M8 0v16M0 8h16"/></svg></div>
    <div class="faq-item open">
      <div class="faq-q">Roof flashing plays an important role in leak prevention most vulnerable areas?<svg viewBox="0 0 16 16"><path d="M0 8h16"/></svg></div>
      <div class="faq-a">Our highly-skilled technicians will expertly diagnose your problem areas and provide you solution to your specific need.</div>
    </div>
  </div>
</section>

<footer class="footer">
  <div class="f-brand">BRVT Roofing</div>
  <p class="f-about">Lorem Ipsum is simply dummy text of the printing and typesetting industry</p>
  <div class="f-social"><span></span><span></span><span></span><span></span><span></span></div>
  <div class="f-col links" style="left:390px"><h4>QUICK LINKS</h4><ul><li>Home</li><li>About Us</li><li>Services</li><li>Why Choose</li><li>Our Gallery</li></ul></div>
  <div class="f-col" style="left:578px"><h4>INFORMATIONS</h4><ul><li>Privacy Policy</li><li>Terms Of Conditions</li><li>Why Mass Torts Now</li><li>Site Map</li><li>Support</li></ul></div>
  <div class="f-col" style="left:836px"><h4>CONTACTS</h4>
    <div style="margin-top:28px">
      <div class="contact-row"><svg viewBox="0 0 24 24"><path d="M12 22s7-7 7-12a7 7 0 00-14 0c0 5 7 12 7 12z"/><circle cx="12" cy="10" r="2.5"/></svg>2140 Harbor Lane, unit 18<br>Riverton, NY 11201</div>
      <div class="contact-row"><svg viewBox="0 0 24 24"><rect x="3" y="5" width="18" height="14"/><path d="M3 6l9 7 9-7"/></svg>hello@brvtroofing.example</div>
      <div class="contact-row"><svg viewBox="0 0 24 24"><path d="M5 3h4l2 5-3 2a11 11 0 006 6l2-3 5 2v4a2 2 0 01-2 2A17 17 0 013 5a2 2 0 012-2z"/></svg>(800) 555-0192</div>
    </div>
  </div>
  <div class="f-rule"></div>
  <p class="f-copy">Copyrights © 2024 BRVT CONSTRUCTION OF NY ROOFING - All Rights Reserved</p>
</footer>

</body>
</html>
```